Business Card Design for Varomir Facility Services

We are looking for a Business Card Design for the Company "Varomir Facility Services."
Front side:
- Company Logo (small)
- Company Name, address, pohone, website and personal data.
- white background, for text e.g. company colors (blue or green like in the logo)
Please use following data:
Company data:
Varomir Facility Services Kostelac
Birkenhaldweg 14
6330 Cham
www.varomir-fs.ch
Person data:
Tarik Kostelac
Geschäftsführer
+41 76 519 47 83
info@varomir-fs.ch
Back side:
could be colored in blue or green
please use a big logo sing and some smaller icons to say what is all beeing offered in facility services, like cleaning, maintenance cleaning
industrial cleaning, caretaking, gardening, disposal. There is no need for everyone of the icons if there are similar or an icon is standing for more of them.
colors to use:
blue: HEX 246BB0
green: HEX 52B33E

```html
<!DOCTYPE html>
<html lang="de">
<head>
<meta charset="utf-8">
<title>Varomir Facility Services – Visitenkarte</title>
<link href="https://fonts.googleapis.com/css2?family=Roboto:wght@400;700;900&display=swap" rel="stylesheet">
<style>
  :root {
    --blue: #246BB0;
    --blue-dark: #1E5FA8;
    --green: #52B33E;
    --ink: #1b1b1b;
    --white: #ffffff;
    --stage: #e4e4e6;
  }
  * { box-sizing: border-box; margin: 0; padding: 0; }
  html, body { width: 1200px; height: 1200px; overflow: hidden; }
  body {
    background: var(--stage);
    font-family: "Roboto", Arial, sans-serif;
    position: relative;
  }
  .card {
    position: absolute;
    left: 160px;
    width: 880px;
    height: 503px;
    border-radius: 28px;
    overflow: hidden;
  }

  /* Back side */
  .card-back { top: 60px; background: var(--blue); color: var(--white); }
  .back-brand {
    position: absolute; top: 70px; left: 0; right: 0;
    text-align: center; font-weight: 700;
  }
  .back-brand .brand-dot {
    display: block; width: 70px; height: 70px; margin: 0 auto 22px;
    border-radius: 50%; background: var(--white);
  }
  .back-brand .brand-name { display: block; font-size: 92px; letter-spacing: 6px; line-height: 1; }
  .back-brand .brand-sub { display: block; font-size: 30px; letter-spacing: 8px; margin-top: 10px; }
  .services {
    position: absolute; top: 330px; left: 0; right: 0;
    display: flex; justify-content: center; gap: 56px;
  }
  .service { width: 130px; text-align: center; }
  .service svg { width: 96px; height: 96px; display: block; margin: 0 auto 10px; }
  .service-label { font-size: 15px; font-weight: 700; letter-spacing: .5px; line-height: 1.15; }

  /* Front side */
  .card-front { top: 627px; background: var(--white); }
  .front-brand {
    position: absolute; top: 46px; left: 50px;
    display: flex; align-items: center; gap: 16px;
    color: var(--blue); font-weight: 700;
  }
  .front-brand .brand-dot { width: 44px; height: 44px; border-radius: 50%; background: var(--green); }
  .front-brand .brand-name { font-size: 48px; letter-spacing: 3px; line-height: 1; }
  .front-brand .brand-sub { font-size: 20px; letter-spacing: 5px; margin-top: 6px; display: block; }
  .divider {
    position: absolute; top: 300px; left: 50px; right: 50px;
    height: 1.5px; background: var(--ink);
  }
  .company { position: absolute; top: 314px; left: 50px; line-height: 1.3; }
  .company-name { color: var(--blue); font-weight: 700; font-size: 22px; }
  .company-line { color: var(--ink); font-size: 21px; }
  .person { position: absolute; right: 50px; top: 228px; text-align: right; }
  .person-name { color: var(--blue); font-weight: 900; font-size: 36px; line-height: 1.05; }
  .person-title { color: var(--ink); font-size: 21px; margin-top: 4px; }
  .contacts {
    position: absolute; right: 50px; top: 312px; text-align: right;
    font-size: 21px; color: var(--ink); line-height: 1.4;
  }
  .contact { display: flex; justify-content: flex-end; align-items: center; gap: 10px; }
  .contact svg { width: 20px; height: 20px; flex: none; }
  .contact .accent { color: var(--blue); font-weight: 700; }
  .front-bands { position: absolute; left: 0; bottom: 0; width: 880px; height: 110px; }
</style>
</head>
<body>

<section class="card card-back" aria-label="Rückseite">
  <div class="back-brand">
    <span class="brand-dot"></span>
    <span class="brand-name">VAROMIR</span>
    <span class="brand-sub">FACILITY SERVICES</span>
  </div>

  <div class="services">
    <div class="service">
      <svg viewBox="0 0 96 96" fill="none" stroke="#fff" stroke-width="4" aria-hidden="true">
        <circle cx="48" cy="48" r="44"/>
        <line x1="48" y1="20" x2="48" y2="46"/>
        <rect x="32" y="46" width="32" height="10" fill="#fff"/>
        <path d="M32 56 L28 74 H68 L64 56"/>
      </svg>
      <div class="service-label">MAINTENANCE<br>CLEANING</div>
    </div>
    <div class="service">
      <svg viewBox="0 0 96 96" fill="none" stroke="#fff" stroke-width="4" aria-hidden="true">
        <circle cx="48" cy="48" r="44"/>
        <path d="M48 72 C20 54 24 28 38 28 C44 28 48 34 48 38 C48 34 52 28 58 28 C72 28 76 54 48 72 Z"/>
      </svg>
      <div class="service-label">CARETAKING</div>
    </div>
    <div class="service">
      <svg viewBox="0 0 96 96" fill="none" stroke="#fff" stroke-width="4" aria-hidden="true">
        <circle cx="48" cy="48" r="44"/>
        <circle cx="48" cy="30" r="8"/>
        <line x1="48" y1="38" x2="48" y2="54"/>
        <path d="M32 54 H64 L60 74 H36 Z" fill="#fff"/>
      </svg>
      <div class="service-label">GARDENING</div>
    </div>
    <div class="service">
      <svg viewBox="0 0 96 96" fill="none" stroke="#fff" stroke-width="4" aria-hidden="true">
        <circle cx="48" cy="48" r="44"/>
        <line x1="28" y1="30" x2="68" y2="30"/>
        <rect x="42" y="24" width="12" height="6"/>
        <path d="M32 30 L35 74 H61 L64 30"/>
        <line x1="42" y1="38" x2="42" y2="66"/>
        <line x1="48" y1="38" x2="48" y2="66"/>
        <line x1="54" y1="38" x2="54" y2="66"/>
      </svg>
      <div class="service-label">DISPOSAL</div>
    </div>
  </div>
</section>

<section class="card card-front" aria-label="Vorderseite">
  <div class="front-brand">
    <span class="brand-dot"></span>
    <div>
      <span class="brand-name">VAROMIR</span>
      <span class="brand-sub">FACILITY SERVICES</span>
    </div>
  </div>

  <div class="person">
    <div class="person-name">Tarik Kostelac</div>
    <div class="person-title">Geschäftsführer</div>
  </div>

  <div class="divider"></div>

  <div class="company">
    <div class="company-name">Varomir Facility Services Kostelac</div>
    <div class="company-line">Birkenhaldweg 14</div>
    <div class="company-line">6330 Cham</div>
  </div>

  <div class="contacts">
    <div class="contact">+41 76 519 47 83
      <svg viewBox="0 0 24 24" aria-hidden="true"><path fill="#246BB0" d="M6.6 10.8a15 15 0 0 0 6.6 6.6l2.2-2.2a1 1 0 0 1 1-.25 11.4 11.4 0 0 0 3.6.57 1 1 0 0 1 1 1V20a1 1 0 0 1-1 1A17 17 0 0 1 3 4a1 1 0 0 1 1-1h3.5a1 1 0 0 1 1 1c0 1.25.2 2.45.57 3.57a1 1 0 0 1-.25 1z"/></svg>
    </div>
    <div class="contact">info@varomir-fs.ch
      <svg viewBox="0 0 24 24" aria-hidden="true"><rect x="2" y="5" width="20" height="14" rx="2" fill="#246BB0"/><path d="M3 6l9 7 9-7" fill="none" stroke="#fff" stroke-width="1.8"/></svg>
    </div>
    <div class="contact"><span>www.<span class="accent">varomir-fs</span>.ch</span>
      <svg viewBox="0 0 24 24" fill="none" stroke="#246BB0" stroke-width="1.8" aria-hidden="true"><circle cx="12" cy="12" r="9.5"/><ellipse cx="12" cy="12" rx="4" ry="9.5"/><line x1="2.5" y1="12" x2="21.5" y2="12"/></svg>
    </div>
  </div>

  <svg class="front-bands" viewBox="0 0 880 110" preserveAspectRatio="none" aria-hidden="true">
    <path d="M0 38 H430 L432 48 H0 Z" fill="var(--green)"/>
    <path d="M0 56 H420 C445 56 450 42 480 42 H880 V110 H0 Z" fill="var(--blue)"/>
  </svg>
</section>

</body>
</html>
```